Private Investigation Business Card Design

I need a business card for a new private investigation company named Brisk Inquiries. I perform mainly surveillance jobs, vehicle repossessions, document serves etc. The final design should aim for a professional look. The logo has a magnifying glass with stick man arms and legs and is in a running action to show the "Brisk" aspect of the name. If the colour scheme could remain the same as the website www.briskinquiries-demo.com.au with silvers,blacks and a couple electric blue highlights.
Industry/Entity Type
Business
Contact Information for Business Card
Morgan Kellaway
Brisk Inquiries
0487316204
PO Box 58, Carnwell NSW 2291
info@briskinquiries-demo.com.au
www.briskinquiries-demo.com.au
Look and feel

```html
<!DOCTYPE html>
<html lang="en">
<head>
<meta charset="utf-8">
<title>Brisk Inquiries – Business Card</title>
<link href="https://fonts.googleapis.com/css2?family=Arimo:wght@400;700&display=swap" rel="stylesheet">
<style>
  :root {
    --stage: #2b2b2b;
    --card-white: #ffffff;
    --ink: #1e1e1e;
    --ink-soft: #444444;
    --silver-light: #e4e4e6;
    --silver-mid: #c3c3c6;
    --silver-dark: #9d9da1;
    --electric-blue: #33a8ee;
    --rule-grey: #b8b8b8;
  }
  * { box-sizing: border-box; margin: 0; padding: 0; }
  html, body { width: 1200px; height: 750px; overflow: hidden; }
  body {
    background: var(--stage);
    font-family: "Arimo", Arial, sans-serif;
    color: var(--ink);
    position: relative;
  }
  .card {
    position: absolute;
    top: 226px;
    width: 520px;
    height: 297px;
    background: var(--card-white);
    overflow: hidden;
  }
  .card-front { left: 60px; }
  .card-back { left: 620px; }

  /* Front */
  .front-mark {
    position: absolute;
    left: 50%;
    top: 62px;
    transform: translateX(-50%);
    display: flex;
    align-items: center;
    gap: 14px;
  }
  .front-mark .dot {
    width: 46px; height: 46px; border-radius: 50%;
    background: var(--silver-mid);
  }
  .front-mark .name {
    font-size: 34px; font-weight: 700; color: var(--ink);
  }
  .front-rule {
    position: absolute;
    left: 110px; right: 110px; top: 212px;
    height: 1px; background: var(--rule-grey);
  }
  .social-row {
    position: absolute;
    left: 50%; top: 201px;
    transform: translateX(-50%);
    display: flex; gap: 6px;
    background: var(--card-white);
    padding: 0 8px;
  }
  .social-row span {
    width: 22px; height: 22px; border-radius: 50%;
    background: var(--ink);
  }

  /* Back */
  .back-panel { position: absolute; inset: 0; }
  .back-mark {
    position: absolute;
    left: 16px; top: 132px;
    display: flex; align-items: center; gap: 8px;
  }
  .back-mark .name { font-size: 19px; font-weight: 700; color: var(--ink-soft); }
  .back-mark .dot { width: 16px; height: 16px; border-radius: 50%; background: var(--silver-dark); }
  .contact {
    position: absolute;
    left: 238px; top: 78px;
    font-size: 11.5px; color: var(--ink-soft); line-height: 1.45;
  }
  .contact .person {
    font-size: 19px; font-weight: 700; color: var(--ink);
    margin-bottom: 14px;
  }
  .contact .address { margin-bottom: 10px; }
  .contact .line { display: flex; align-items: center; gap: 7px; }
  .contact svg { width: 12px; height: 12px; flex: none; }
</style>
</head>
<body>

<section class="card card-front" aria-label="Card front">
  <div class="front-mark">
    <span class="dot"></span>
    <span class="name">Brisk Inquiries</span>
  </div>
  <div class="front-rule"></div>
  <div class="social-row" aria-label="Social channels">
    <span></span><span></span><span></span><span></span>
  </div>
</section>

<section class="card card-back" aria-label="Card back">
  <svg class="back-panel" width="520" height="297" viewBox="0 0 520 297">
    <defs>
      <radialGradient id="silverSheen" cx="0.55" cy="0.45" r="0.7">
        <stop offset="0" stop-color="var(--silver-light)"/>
        <stop offset="0.6" stop-color="var(--silver-mid)"/>
        <stop offset="1" stop-color="var(--silver-dark)"/>
      </radialGradient>
    </defs>
    <path d="M205,0 L205,95 L213,102 L205,109 L205,297 L520,297 L520,0 Z" fill="url(#silverSheen)"/>
    <path d="M205,0 L205,95 L213,102 L205,109 L205,297" fill="none" stroke="var(--electric-blue)" stroke-width="2.5"/>
  </svg>

  <div class="back-mark">
    <span class="name">Brisk Inquiries</span>
    <span class="dot"></span>
  </div>

  <div class="contact">
    <p class="person">Morgan Kellaway</p>
    <p class="address">PO Box 58<br>Carnwell NSW 2291</p>
    <p class="line">
      <svg viewBox="0 0 12 12"><circle cx="6" cy="6" r="6" fill="var(--ink)"/><path d="M3.5,3.2 L5,3 L5.6,4.6 L4.8,5.2 Q5.5,6.7 6.9,7.3 L7.5,6.5 L9,7.1 L8.8,8.6 Q5,8.8 3.5,3.2 Z" fill="#fff"/></svg>
      0487 316 204
    </p>
    <p class="line">
      <svg viewBox="0 0 12 12"><circle cx="6" cy="6" r="6" fill="var(--ink)"/><rect x="3" y="4" width="6" height="4.2" fill="#fff"/><path d="M3,4 L6,6.4 L9,4" fill="none" stroke="var(--ink)" stroke-width="0.8"/></svg>
      info@briskinquiries-demo.com.au
    </p>
    <p class="line">
      <svg viewBox="0 0 12 12"><circle cx="6" cy="6" r="6" fill="var(--ink)"/><path d="M6,2.6 A2.2,2.2 0 0 1 8.2,4.8 C8.2,6.5 6,9.2 6,9.2 C6,9.2 3.8,6.5 3.8,4.8 A2.2,2.2 0 0 1 6,2.6 Z" fill="#fff"/><circle cx="6" cy="4.8" r="0.8" fill="var(--ink)"/></svg>
      www.briskinquiries-demo.com.au
    </p>
  </div>
</section>

</body>
</html>
```